Website design for an Italian restaurant in Amsterdam

I need a design for a client of mine. It is for Teatro Lucerna, an Italian restaurant in Amsterdam.
We are going for a clean, modern look but we also need to realise an authentic feel.
The restaurant is located in an old movie theatre, that is where the name Teatro Lucerna comes from.
Industry/Entity Type
Italian Restaurant
Number of Pages Required
1 page
Font styles to use
Sans Serif
Colors
Designer to choose colors to be used in the design.

```html
<!DOCTYPE html>
<html lang="en">
<head>
<meta charset="utf-8">
<title>Teatro Lucerna – Italian Restaurant Amsterdam</title>
<link href="https://fonts.googleapis.com/css2?family=Roboto+Condensed:wght@400;700&family=Open+Sans:wght@400;600&family=Raleway:wght@300;400&family=Playfair+Display:wght@700&display=swap" rel="stylesheet">
<style>
:root{
  --red:#e2401f;
  --red-dark:#c9341a;
  --ink:#1d1d1d;
  --black:#111111;
  --dark:#1b1b1b;
  --grey-text:#777777;
  --light:#f3f3f3;
  --line:#e4e4e4;
  --white:#ffffff;
}
*{margin:0;padding:0;box-sizing:border-box}
html,body{width:1200px;height:3863px;overflow:hidden}
body{font-family:"Open Sans",Arial,sans-serif;color:var(--ink);background:var(--white);position:relative}
.section{position:absolute;left:0;width:1200px}
.abs{position:absolute}
.cond{font-family:"Roboto Condensed","Arial Narrow",sans-serif}

/* header */
.site-header{top:0;height:113px;background:var(--black)}
.brand{left:134px;top:40px;color:var(--white);font-family:"Roboto Condensed",sans-serif;font-size:20px;letter-spacing:2px;display:flex;align-items:center;gap:10px}
.brand-dot{width:14px;height:14px;border-radius:50%;background:var(--red)}
.top-contact{top:22px;left:762px;color:var(--white);font-size:14px;display:flex;align-items:center;gap:8px}
.lang{top:24px;left:962px;color:var(--white);font-size:11px;display:flex;align-items:center;gap:6px;letter-spacing:.5px}
.flag{width:18px;height:11px;background:linear-gradient(#2b3f8a,#2b3f8a);border:1px solid #c22}
.main-nav{top:68px;right:134px;display:flex;gap:28px}
.main-nav a{color:var(--white);text-decoration:none;font-family:"Roboto Condensed",sans-serif;font-size:14px;text-transform:uppercase;letter-spacing:.3px}

/* hero */
.hero{top:113px;height:582px;background:radial-gradient(ellipse at 62% 35%,#6a5646 0%,#3a2e26 35%,#1c1815 70%,#121110 100%)}
.hero-title{left:134px;top:195px;color:var(--white);font-family:"Roboto Condensed",sans-serif;font-weight:700;font-size:54px;line-height:58px;text-transform:uppercase}
.btn{display:inline-block;background:var(--red);color:var(--white);font-family:"Roboto Condensed",sans-serif;font-size:14px;text-transform:uppercase;text-align:center;letter-spacing:.5px}
.hero-btn{left:134px;top:330px;width:163px;height:41px;line-height:41px}
.arrow{top:232px;width:30px;height:30px}
.booking{top:510px;left:134px;display:flex;gap:14px}
.field{height:37px;background:var(--white);color:#555;font-size:11px;line-height:37px;padding-left:10px;position:relative}
.field .caret{position:absolute;right:10px;top:15px;width:7px;height:7px;border-right:1px solid #888;border-bottom:1px solid #888;transform:rotate(45deg)}
.booking .btn{height:37px;line-height:37px;width:144px}

/* welcome */
.welcome{top:695px;height:528px;background:var(--white)}
.welcome-panel{left:59px;top:26px;width:662px;height:502px;background:var(--light)}
.welcome-photo{left:631px;top:0;width:515px;height:528px;background:radial-gradient(circle at 45% 40%,#f3efe9 0%,#e6e0d6 35%,#d7d1c8 60%,#ece8e2 100%)}
.welcome-title{left:136px;top:105px;font-family:"Roboto Condensed",sans-serif;font-weight:700;font-size:26px;text-transform:uppercase;color:var(--ink)}
.welcome-title span{color:var(--red)}
.welcome-sub{left:136px;top:160px;font-size:13px;font-weight:600;text-transform:uppercase}
.welcome-hours{left:136px;top:186px;font-size:13px;color:var(--red)}
.welcome-text{left:136px;top:228px;width:440px;font-size:11.5px;line-height:23px;color:#555}
.read-more{left:136px;top:385px;width:126px;height:34px;line-height:32px;border:1.5px solid var(--red);border-radius:17px;color:var(--red);font-size:11px;font-weight:600;text-align:center;text-transform:uppercase}

/* features */
.features{top:1223px;height:554px;background:linear-gradient(135deg,#2a2624 0%,#1a1918 45%,#232221 100%)}
.feature{top:108px;width:296px;height:322px;background:var(--red);color:var(--white);text-align:center;padding:30px 26px 0;
  clip-path:polygon(16px 0,calc(100% - 16px) 0,100% 16px,100% calc(100% - 16px),calc(100% - 16px) 100%,16px 100%,0 calc(100% - 16px),0 16px)}
.feature h3{font-family:"Roboto Condensed",sans-serif;font-size:22px;text-transform:uppercase;font-weight:700}
.feature .rule{width:44px;height:2px;background:var(--white);margin:16px auto 16px}
.feature p{font-size:11.5px;line-height:20px}
.feature svg{margin-top:16px}

/* menu */
.menu{top:1777px;height:605px;background:var(--white)}
.section-title{width:1200px;text-align:center;font-family:"Roboto Condensed",sans-serif;font-weight:700;font-size:36px}
.menu .section-title{top:76px;color:var(--ink)}
.dish{top:175px;width:221px;height:324px;border:1px solid var(--line);background:var(--white);text-align:center}
.dish-photo{height:180px;width:100%}
.dish-badge{position:absolute;left:90px;top:160px}
.dish h4{margin-top:32px;font-size:17px;font-weight:400;color:var(--ink)}
.dish p{margin:10px 20px 0;font-size:11px;line-height:17px;color:var(--grey-text)}

/* group menu */
.groupmenu{top:2382px;height:623px;background:radial-gradient(ellipse at 50% 40%,#2e2724 0%,#1c1816 60%,#141210 100%)}
.groupmenu .section-title{top:78px;color:var(--white);text-transform:uppercase}
.group-card{top:172px;width:431px;height:343px;background:var(--white);padding:8px;text-align:center}
.group-photo{width:100%;height:276px}
.group-card h4{margin-top:16px;font-family:"Playfair Display",serif;font-size:19px;color:var(--ink)}
.group-card h4 span{color:var(--red)}

/* newsletter + hours */
.info{top:3005px;height:471px;background:var(--light)}
.info-divider{left:618px;top:90px;width:1px;height:300px;background:#dcdcdc}
.info-col{top:0;width:440px;text-align:center}
.info-col .kicker{font-family:"Raleway",sans-serif;font-size:26px;text-transform:uppercase;letter-spacing:1px;color:#333}
.info-col .big{font-family:"Raleway",sans-serif;font-weight:300;font-size:46px;text-transform:uppercase;letter-spacing:3px;color:#333;line-height:50px}
.info-input{width:281px;height:39px;background:var(--white);border:1px solid #ddd;margin:28px auto 0;font-size:10px;color:#777;line-height:37px}
.info-col .btn{height:36px;line-height:36px;font-size:13px;font-weight:700}
.info-hours{font-size:13px;line-height:22px;color:#444;margin-top:18px}

/* footer */
.site-footer{top:3476px;height:387px;background:var(--black);color:var(--white)}
.footer-head{top:66px;font-family:"Roboto Condensed",sans-serif;font-weight:700;font-size:16px;text-transform:uppercase}
.contact-row{left:134px;display:flex;gap:16px;font-size:11.5px;line-height:17px}
.signup-text{left:417px;top:104px;width:270px;font-size:11px;line-height:18px}
.footer-input{left:417px;top:148px;width:266px;height:38px;background:var(--white);color:#666;font-size:10px;line-height:38px;padding-left:12px}
.subscribe{left:417px;top:204px;width:92px;height:36px;line-height:36px;font-size:11px}
.quick-links{left:757px;top:108px;list-style:none;font-size:11px;line-height:20px}
.footer-brand{left:900px;top:78px;width:166px;text-align:center;font-family:"Roboto Condensed",sans-serif;font-size:17px;letter-spacing:2px}
.socials{left:938px;top:150px;display:flex;gap:6px}
.socials span{width:20px;height:20px;border-radius:50%;border:1.5px solid var(--white)}
.copyright{top:333px;width:1200px;text-align:center;font-size:11px;color:#bbbbbb}
</style>
</head>
<body>

<header class="section site-header">
  <div class="abs brand"><span class="brand-dot"></span>TEATRO LUCERNA</div>
  <div class="abs top-contact">
    <svg width="22" height="22" viewBox="0 0 22 22"><circle cx="11" cy="11" r="10" fill="none" stroke="#fff" stroke-width="1.4"/><path d="M7.5 6.5l2 0 1 2.5-1.3 1c.6 1.3 1.5 2.2 2.8 2.8l1-1.3 2.5 1v2c0 .6-.5 1-1 1-4 0-7-3-7-7 0-.5.4-1 1-1z" fill="#fff"/></svg>
    (+31) 20 555 0142
  </div>
  <div class="abs lang">ENGLISH <span class="flag"></span>
    <svg width="8" height="6" viewBox="0 0 8 6"><path d="M1 1l3 3 3-3" stroke="#fff" fill="none"/></svg>
  </div>
  <nav class="abs main-nav">
    <a href="#">Home</a><a href="#">About us</a><a href="#">Menu (new)</a><a href="#">Groupmenu</a><a href="#">Reservation</a><a href="#">Contact us</a>
  </nav>
</header>

<section class="section hero" role="img" aria-label="Chef plating a dish in a warm, dimly lit restaurant kitchen">
  <svg class="abs arrow" style="left:82px" viewBox="0 0 30 30"><path d="M18 8l-7 7 7 7" stroke="#fff" stroke-width="2.5" fill="none"/></svg>
  <svg class="abs arrow" style="left:1080px" viewBox="0 0 30 30"><path d="M12 8l7 7-7 7" stroke="#fff" stroke-width="2.5" fill="none"/></svg>
  <h1 class="abs hero-title">Authentic<br>Italian Cuisine</h1>
  <a class="abs btn hero-btn">Reservations</a>
  <form class="abs booking">
    <div class="field" style="width:186px">Name<span class="caret"></span></div>
    <div class="field" style="width:183px">Date&amp;Time<span class="caret"></span></div>
    <div class="field" style="width:183px">Menu<span class="caret"></span></div>
    <div class="field" style="width:185px">Phone Number</div>
    <a class="btn">Reservations</a>
  </form>
</section>

<section class="section welcome">
  <div class="abs welcome-panel"></div>
  <div class="abs welcome-photo" role="img" aria-label="Fresh salad bowl with tomatoes, lemon and cutlery on a white wooden table"></div>
  <h2 class="abs welcome-title">Welcome to <span>Teatro Lucerna</span></h2>
  <p class="abs welcome-sub">Now open on Sundays !</p>
  <p class="abs welcome-hours">Tue - Sat 18:00 - 23:00, Sun &amp; Mon Closed</p>
  <p class="abs welcome-text">Our kitchen follows the seasons and the markets of Italy, with fresh pasta rolled every morning and sauces simmered slowly for hours. Inside the restored cinema hall you dine beneath the old projector lights, surrounded by the stories of a hundred films. Come for a quick lunch, stay for a long dinner with friends and family.</p>
  <a class="abs read-more">Read more ›</a>
</section>

<section class="section features">
  <article class="abs feature" style="left:134px">
    <h3>Italian Restaurant</h3><div class="rule"></div>
    <p>Classic recipes from every region of Italy, cooked with care and served in the warm glow of our historic theatre hall.</p>
    <svg width="64" height="56" viewBox="0 0 64 56" fill="none" stroke="#fff" stroke-width="2"><path d="M10 38a22 22 0 0 1 44 0z"/><path d="M4 42h56"/><circle cx="32" cy="13" r="3"/><path d="M22 46l-6 6h32"/></svg>
  </article>
  <article class="abs feature" style="left:452px">
    <h3>Kitchen &amp; Bar</h3><div class="rule"></div>
    <p>An open kitchen and a long marble bar where cocktails, antipasti and small plates are prepared right before your eyes.</p>
    <svg width="64" height="56" viewBox="0 0 64 56" fill="none" stroke="#fff" stroke-width="2"><path d="M10 30h44M32 30v22M18 52h28"/><path d="M6 20v32M6 38h10v14"/><path d="M58 20v32M58 38H48v14"/><path d="M26 10v14M30 8v16M36 14h6l-3 10"/></svg>
  </article>
  <article class="abs feature" style="left:770px">
    <h3>Our Beverages</h3><div class="rule"></div>
    <p>Italian wines by the glass or bottle, craft beers, fresh juices and our own limoncello to round off every evening.</p>
    <svg width="64" height="56" viewBox="0 0 64 56" fill="none" stroke="#fff" stroke-width="2"><path d="M10 12h16c0 12-4 18-8 18s-8-6-8-18zM18 30v18M11 50h14"/><path d="M42 4h6v12c4 3 5 6 5 10v26H37V26c0-4 1-7 5-10z"/><path d="M37 32h16"/></svg>
  </article>
</section>

<section class="section menu">
  <h2 class="abs section-title">Menu (new)</h2>
  <article class="abs dish" style="left:131px">
    <div class="dish-photo" role="img" aria-label="Antipasti platter with tomatoes and olives" style="background:linear-gradient(135deg,#b8432c,#6f3a2a 60%,#c9a070)"></div>
    <svg class="dish-badge" width="40" height="40" viewBox="0 0 40 40"><circle cx="20" cy="20" r="20" fill="var(--red)"/><path d="M14 14l12 12M26 14l-12 12" stroke="#fff" stroke-width="2"/></svg>
    <h4>Antipasti</h4>
    <p>Cured meats, marinated vegetables and warm bread to start the meal.</p>
  </article>
  <article class="abs dish" style="left:371px">
    <div class="dish-photo" role="img" aria-label="Fruit tart with berries" style="background:linear-gradient(135deg,#4d3a2c,#a1523c 50%,#e0b860)"></div>
    <svg class="dish-badge" width="40" height="40" viewBox="0 0 40 40"><circle cx="20" cy="20" r="20" fill="var(--red)"/><path d="M14 14l12 12M26 14l-12 12" stroke="#fff" stroke-width="2"/></svg>
    <h4>Dolce</h4>
    <p>Tiramisu, panna cotta and fruit tarts made fresh in our kitchen.</p>
  </article>
  <article class="abs dish" style="left:608px">
    <div class="dish-photo" role="img" aria-label="Green salad with tomatoes" style="background:linear-gradient(135deg,#3f5a2a,#6f8c3a 50%,#2f3a24)"></div>
    <svg class="dish-badge" width="40" height="40" viewBox="0 0 40 40"><circle cx="20" cy="20" r="20" fill="var(--red)"/><path d="M14 14l12 12M26 14l-12 12" stroke="#fff" stroke-width="2"/></svg>
    <h4>Le Insalate</h4>
    <p>Crisp seasonal salads with olive oil, lemon and shaved parmesan.</p>
  </article>
  <article class="abs dish" style="left:847px">
    <div class="dish-photo" role="img" aria-label="Side dish of roasted vegetables" style="background:linear-gradient(135deg,#c4b49c,#8f6a48 50%,#d9cbb8)"></div>
    <svg class="dish-badge" width="40" height="40" viewBox="0 0 40 40"><circle cx="20" cy="20" r="20" fill="var(--red)"/><path d="M14 14l12 12M26 14l-12 12" stroke="#fff" stroke-width="2"/></svg>
    <h4>Contorni</h4>
    <p>Roasted potatoes, grilled greens and other sides to share.</p>
  </article>
</section>

<section class="section groupmenu">
  <h2 class="abs section-title">Groupmenu</h2>
  <article class="abs group-card" style="left:142px">
    <div class="group-photo" role="img" aria-label="Bruschetta with cured ham and tomato" style="background:radial-gradient(circle at 45% 50%,#c65a3a 0%,#9e3b2a 35%,#e7e2da 75%)"></div>
    <h4>Groupmenu Speciale <span>(€ 34,50)</span></h4>
  </article>
  <article class="abs group-card" style="left:615px">
    <div class="group-photo" role="img" aria-label="Risotto with mushrooms and green asparagus" style="background:radial-gradient(circle at 50% 50%,#a88a5e 0%,#6e6a3a 40%,#3a3a2a 80%)"></div>
    <h4>Groupmenu Royal <span>(€ 49,50)</span></h4>
  </article>
</section>

<section class="section info">
  <div class="abs info-divider"></div>
  <div class="abs info-col" style="left:138px;padding-top:88px">
    <svg width="70" height="72" viewBox="0 0 70 72" fill="none" stroke="#222" stroke-width="2"><path d="M8 30L35 10l27 20v34H8z"/><path d="M8 30l27 20 27-20"/><path d="M16 36V18h38v18"/><path d="M22 24h26M22 30h20"/></svg>
    <p class="kicker">Email</p>
    <p class="big">Newsletter</p>
    <div class="info-input">Enter email</div>
    <a class="btn" style="width:123px;margin-top:21px">Sign up</a>
  </div>
  <div class="abs info-col" style="left:630px;padding-top:88px">
    <svg width="70" height="72" viewBox="0 0 70 72" fill="none" stroke="#222" stroke-width="2"><path d="M35 6l-20 24M35 6l20 24"/><circle cx="35" cy="6" r="3" fill="#222"/><rect x="8" y="30" width="54" height="34" rx="3"/><text x="35" y="53" text-anchor="middle" font-family="Roboto Condensed, sans-serif" font-size="14" font-weight="700" fill="#222" stroke="none">OPEN</text></svg>
    <p class="kicker">Restaurant opening</p>
    <p class="big">Times</p>
    <p class="info-hours">Tue - Sat 18:00 - 23:00<br>Sun &amp; Mon Closed</p>
    <a class="btn" style="width:157px;margin-top:21px">Reserve a table</a>
  </div>
</section>

<footer class="section site-footer">
  <h5 class="abs footer-head" style="left:134px">Contact us</h5>
  <div class="abs contact-row" style="top:112px">
    <svg width="14" height="18" viewBox="0 0 14 18" fill="none" stroke="#fff" stroke-width="1.4"><path d="M7 17s6-6 6-10A6 6 0 0 0 1 7c0 4 6 10 6 10z"/><circle cx="7" cy="7" r="2"/></svg>
    <span>Teatro Lucerna<br>Lindengracht 72<br>1015KL Amsterdam</span>
  </div>
  <div class="abs contact-row" style="top:176px">
    <svg width="14" height="14" viewBox="0 0 14 14"><path d="M2 1h3l1.5 3.5-2 1.3a8 8 0 0 0 3.7 3.7l1.3-2L13 9v3c0 .6-.4 1-1 1C6 13 1 8 1 2c0-.6.4-1 1-1z" fill="none" stroke="#fff" stroke-width="1.3"/></svg>
    <span>Phone : (+31) 20 555 0142</span>
  </div>
  <div class="abs contact-row" style="top:210px">
    <svg width="16" height="12" viewBox="0 0 16 12" fill="none" stroke="#fff" stroke-width="1.3"><rect x="1" y="1" width="14" height="10"/><path d="M1 1l7 6 7-6"/></svg>
    <span>info@teatrolucerna.example</span>
  </div>

  <h5 class="abs footer-head" style="left:417px">Sign up to receive email</h5>
  <p class="abs signup-text">Get our seasonal menus, events and offers straight to your inbox.</p>
  <div class="abs footer-input">Enter Name</div>
  <a class="abs btn subscribe">Subscribe</a>

  <h5 class="abs footer-head" style="left:757px">Quick links</h5>
  <ul class="abs quick-links">
    <li>Home</li><li>About Us</li><li>Menu</li><li>Reservations</li><li>Groupmenu</li><li>Contact Us</li>
  </ul>

  <div class="abs footer-brand">TEATRO LUCERNA</div>
  <div class="abs socials"><span></span><span></span><span></span><span></span></div>

  <p class="abs copyright">Copyright © Teatro Lucerna 2018. All rights reserved.</p>
</footer>

</body>
</html>
```